Web Design Velmora Tech

• An Overview of Velmora Tech for reference: We use to be a component manufacturing company. We sold to customers in USA and manage the builds in China using many manufacturing partners. We had a web site that served this market but we have transitioned over the last several years into “A unique design, development and program management company” It is this message we want to put up on the web now. We provide the design support, we help develop and test a new product for our customers and we provide the manufactured produce once we have transitioned it into production.
• The Target Market: Our customers are all high tech. Each product we produce is custom designed and sold only to one a specific customer. We work with a limited number of customer and sell to new customers by word of mouth and referrals. The web site is to provide a back ground check of any new referral so they can see who we are and our basic capabilities. It is not designed to sell customers or to find new customers but provide a background check to new potential customers.
• Pages Required: We estimate 12:
o Home/Title page is page 1 of PDF. It would have buttons to select other pages
o Names of other pages would be (short titles below if on button, if pull down menu the full title of slide)
 USA Facilities
 China Facilities
 Enclosures
 Antennas
 Connectors
 Cables
 EMI Shields
 Overlays
 Process Development
 BrisaLink
 Contact Us (???) >> new page which we are not sure if we should or should not add.
• Design Specifics; attached is our logo, a PDF and PowerPoint slides showing the views we desire. We like these layouts, but perhaps a better one may be suggested for some artistic reason or layout. It should be clean, simple and user intuitive. We like the off white background and use for most of our presentations. One should be able to go from any screen to any other screen. The quote must include both design and implementation onto our web site which is http://velmoratechworks.example/
• Design Process:
We would like to see concepts of the Landing/Homepage, and an internal page initially. Feedback will be provided and you will be asked to continue if your layout is on the correct track.

• Implementation: Desire designer/implimentor to set up on their server. Allow us to test and edit on their site. We will provide password for implementation on our site after final approval.

Target Market(s)

• The Target Market: see above task descripiton

Industry/Entity Type

It Company

Requirements
Must have
• • Pages Required: We estimate 12:
 USA Facilities
 China Facilities
 Enclosures
 Antennas
 Connectors
 Cables
 EMI Shields
 Overlays
 Process Development
 BrisaLink

Must have the implementation phase include in quote. see task description above
Should not have
• Should not be complex or long time loading.
Do not want any twitter or promotional add on functions.

```html
<!DOCTYPE html>
<html lang="en">
<head>
<meta charset="utf-8">
<title>Velmora Tech — Design, Development and Program Management</title>
<link rel="stylesheet" href="https://fonts.googleapis.com/css2?family=Anton&family=Oswald:wght@500&family=Montserrat:wght@400;600;700;800&display=swap">
<style>
:root{
  --navy:#353a6b;
  --blue:#0a72bc;
  --text:#6b6b6b;
  --muted:#8a8a8a;
  --line:#e3e3e3;
  --map:#f1f1f1;
  --pin:#d93a26;
  --pin-dark:#8e1a10;
  --white:#ffffff;
}
*{box-sizing:border-box;margin:0;padding:0}
html,body{width:1200px;height:885px;overflow:hidden;background:var(--white)}
body{position:relative;font-family:"Montserrat",Arial,sans-serif;color:var(--text)}
.abs{position:absolute}

.call{left:162px;top:47px;display:flex;align-items:center;gap:8px;font-size:11.5px;color:var(--muted)}
.call-icon{width:26px;height:26px}
.call strong{font-size:17px;color:var(--blue);font-weight:600;margin-left:3px}

.top-links{left:692px;top:59px;font-size:9.5px;font-weight:600;color:var(--blue);white-space:nowrap}
.top-links .sep{margin:0 6px}

.main-nav{left:160px;top:84px;width:880px;height:56px;background:var(--navy)}
.nav-shadow{left:170px;top:140px;width:860px;height:24px;background:radial-gradient(ellipse at 50% 0,rgba(0,0,0,.18),rgba(0,0,0,0) 70%)}
.nav-item{top:108px;font-size:10px;font-weight:700;color:var(--white);letter-spacing:-.4px;white-space:nowrap}
.nav-sep{top:104px;width:0;height:18px;border-left:1px dotted rgba(255,255,255,.4)}

.brand{left:494px;top:14px;width:176px;height:176px;border-radius:50%;background:var(--white);border:4px solid #dcdcdc;display:flex;align-items:center;justify-content:center;z-index:2}
.brand-disc{width:156px;height:156px;border-radius:50%;background:var(--blue);display:flex;align-items:center;justify-content:center;text-align:center;color:var(--white);font-weight:800;font-size:24px;line-height:1.05}
.brand-shadow{left:510px;top:194px;width:150px;height:14px;background:radial-gradient(ellipse,rgba(0,0,0,.12),rgba(0,0,0,0) 70%)}

.world-map{left:200px;top:180px;width:800px;height:380px;background:radial-gradient(ellipse at 50% 50%,var(--map) 0%,#f7f7f7 55%,rgba(255,255,255,0) 75%)}
.pin{width:42px;height:56px}
.address{font-size:9px;font-weight:600;color:var(--blue);line-height:11.5px}

.tagline{left:326px;top:512px;font-family:"Oswald",sans-serif;font-weight:500;font-size:23px;color:var(--blue);letter-spacing:-.4px;line-height:1;white-space:nowrap}
.headline{left:324px;top:535px;font-family:"Anton",sans-serif;font-weight:400;font-size:70px;color:var(--navy);line-height:1;letter-spacing:-1px;white-space:nowrap}

.rule{left:160px;width:880px;height:0;border-top:1px dotted var(--line)}
.col-rule{top:656px;height:132px;width:0;border-left:1px dotted var(--line)}

.col-title{top:656px;font-size:18px;font-weight:800;color:var(--blue);letter-spacing:-.6px}
.col-text{font-size:10px;line-height:13.6px;color:var(--text)}
.product-list{list-style:none;font-size:10px;line-height:19px;color:var(--text)}
.btn{top:758px;height:20px;border-radius:4px;background:var(--blue);color:var(--white);font-size:10px;font-weight:700;display:flex;align-items:center;justify-content:center;letter-spacing:-.2px}

.field{left:780px;width:236px;height:28px;border:1px solid #d4d4d4;border-radius:7px;display:flex;align-items:center;font-size:11px;color:var(--muted)}
.field svg{width:16px;height:16px;margin:0 9px 0 14px}
.field .div{height:16px;border-left:1px dotted #bbb;margin-right:11px}

.footer-links{left:180px;top:828px;font-size:10.5px;color:var(--muted);white-space:nowrap}
.copyright{left:180px;top:852px;font-size:9.5px;font-weight:700;color:var(--muted)}
.copyright a{color:var(--blue);text-decoration:none}
</style>
</head>
<body>

<div class="abs call">
  <svg class="call-icon" viewBox="0 0 26 26"><circle cx="13" cy="13" r="12" fill="none" stroke="#3d4470" stroke-width="1.5"/><path d="M9 7c-1.5 1-1.8 3-1 5.5 1 3 3.5 6 6 7 1.5.6 2.8.3 3.6-.6l-2.3-2.3-1.6 1c-1.6-.8-3.3-2.8-4-4.6l1.2-1.4L9 7z" fill="#3d4470"/></svg>
  <span>Call Us TODAY:<strong>0800 555 0199</strong></span>
</div>

<nav class="abs top-links">OVERLAYS<span class="sep">|</span>PROCESS DEVELOPMENT<span class="sep">|</span>BRISALINK<span class="sep">|</span>CONTACT US</nav>

<div class="abs nav-shadow"></div>
<div class="abs main-nav"></div>
<span class="abs nav-item" style="left:180px">USA FACILITIES</span>
<span class="abs nav-sep" style="left:277px"></span>
<span class="abs nav-item" style="left:293px">CHINA FACILITIES</span>
<span class="abs nav-sep" style="left:394px"></span>
<span class="abs nav-item" style="left:413px">ENCLOSURES</span>
<span class="abs nav-item" style="left:693px">ANTENNAS</span>
<span class="abs nav-sep" style="left:762px"></span>
<span class="abs nav-item" style="left:777px">CONNECTORS</span>
<span class="abs nav-sep" style="left:863px"></span>
<span class="abs nav-item" style="left:884px">CABLES</span>
<span class="abs nav-sep" style="left:942px"></span>
<span class="abs nav-item" style="left:960px">EMI SHIELDS</span>

<div class="abs brand-shadow"></div>
<div class="abs brand"><div class="brand-disc">VELMORA<br>TECH</div></div>

<div class="abs world-map" role="img" aria-label="Faint world map showing company locations in the USA and China"></div>

<div class="abs address" style="left:325px;top:298px">48 Orchard Row<br>Suite 210 Fernvale, CA<br>90210</div>
<svg class="abs pin" style="left:284px;top:324px" viewBox="0 0 42 56"><ellipse cx="21" cy="53" rx="8" ry="2" fill="rgba(0,0,0,.12)"/><path d="M21 2C10 2 3 10 3 19c0 11 18 31 18 31s18-20 18-31C39 10 32 2 21 2z" fill="var(--pin)"/><circle cx="21" cy="18" r="7" fill="var(--pin-dark)"/></svg>

<div class="abs address" style="left:810px;top:257px">Lanxi Park District<br>Qinghe Road #12 Suzhou, China<br>215000</div>
<svg class="abs pin" style="left:848px;top:282px" viewBox="0 0 42 56"><ellipse cx="21" cy="53" rx="8" ry="2" fill="rgba(0,0,0,.12)"/><path d="M21 2C10 2 3 10 3 19c0 11 18 31 18 31s18-20 18-31C39 10 32 2 21 2z" fill="var(--pin)"/><circle cx="21" cy="18" r="7" fill="var(--pin-dark)"/></svg>

<h2 class="abs tagline">A UNIQUE DESIGN, DEVELOPMENT AND PROGRAM</h2>
<h1 class="abs headline">MANAGEMENT COMPANY</h1>

<div class="abs rule" style="top:625px"></div>
<div class="abs col-rule" style="left:454px"></div>
<div class="abs col-rule" style="left:748px"></div>

<h3 class="abs col-title" style="left:181px">WHO WE ARE?</h3>
<p class="abs col-text" style="left:181px;top:692px;width:250px">Lorem ipsum dolor sit amet, consectetuer adipiscing elit, sed diam nonummy nibh euismod tincidunt ut laoreet dolore magna aliquam erat volutpat.</p>
<a class="abs btn" style="left:180px;width:80px">Read More...</a>

<h3 class="abs col-title" style="left:479px">OUR PRODUCTS</h3>
<ul class="abs product-list" style="left:480px;top:689px">
  <li>Custom Enclosure Design and Development</li>
  <li>Custom Antenna Design and Development</li>
  <li>Custom Connector Design and Development</li>
</ul>
<a class="abs btn" style="left:480px;width:102px">More Products...</a>

<h3 class="abs col-title" style="left:781px">SIGN UP WITH US</h3>
<div class="abs field" style="top:692px">
  <svg viewBox="0 0 16 16"><path d="M1 6l7-4 7 4v8H1z" fill="#3d3d3d"/><path d="M2 7l6 4 6-4" fill="none" stroke="#fff" stroke-width="1.2"/></svg>
  <span class="div"></span>Enter Your Email Address
</div>
<div class="abs field" style="top:724px">
  <svg viewBox="0 0 16 16"><circle cx="11" cy="5" r="3.5" fill="#3d3d3d"/><path d="M9 7L2 14l1.5 1.5 1.5-1.5 1 1 1-1-1-1 4-4z" fill="#3d3d3d"/></svg>
  <span class="div"></span>Enter Your Password
</div>
<a class="abs btn" style="left:781px;width:80px">Login</a>

<div class="abs rule" style="top:810px"></div>
<nav class="abs footer-links">USA Facilities - China Facilities - Enclosures - Antennas - Connectors - Cables - EMI Shields - Overlays - Process Development - BrisaLink - &nbsp;Contact Us</nav>
<p class="abs copyright">VELMORA TECH © 2013 - &nbsp;<a>Privacy Policy</a></p>

</body>
</html>
```